Website for a new t-shirt company called bolddawnapperal.com

We are looking for a talented web designer to create a website that aligns with our brand's message and identity centered around the theme of "Bold Dawn." The website should be modern, clean, and visually appealing while also being user-friendly and easy to navigate.

We will be using the Big Commerce platform for our online store section, so the designer should have experience in designing websites on this platform.

We would like the website to have the following elements:

A color scheme that aligns with the brand's identity and message
A homepage that showcases our products and message, with clear calls-to-action for visitors to explore further
A blog section that highlights our brand's philosophy and offers advice and tips for people looking to make positive changes in their lives
An "About Us" section that introduces our brand and team and offers insight into our mission and values
A contact form that allows visitors to easily get in touch with us for inquiries or support
We are open to creative suggestions and ideas from the designer, but we would like the website to have a modern and minimalist aesthetic that resonates with our target audience of 20 to 40-year-olds.

```html
<!DOCTYPE html>
<html lang="en">
<head>
<meta charset="utf-8">
<title>Bold Dawn — T-Shirts</title>
<link href="https://fonts.googleapis.com/css2?family=Exo+2:wght@300;400;500;600&display=swap" rel="stylesheet">
<style>
:root{
  --ink:#231f20;
  --text:#1d1d1d;
  --muted:#777;
  --card:#f3f3f3;
  --white:#fff;
  --line:#d9d9d9;
  --c-navy:#0b3a7e;
  --c-slate:#3b4652;
  --c-red:#f5140f;
  --c-teal:#0f8a80;
  --c-pink:#c7338f;
}
*{box-sizing:border-box;margin:0;padding:0}
html,body{width:1200px;height:3375px;overflow:hidden}
body{font-family:"Exo 2",sans-serif;color:var(--text);background:var(--white);position:relative}
.abs{position:absolute}
.promo{top:0;left:0;width:1200px;height:32px;background:var(--ink);color:var(--white);font-size:13px;display:flex;align-items:center;justify-content:center}
.search{left:98px;top:58px;width:207px;height:38px;border:1px solid var(--line);border-radius:6px;font-size:15px;color:#888;padding:0 8px;display:flex;align-items:center;justify-content:space-between}
.brand{left:450px;top:48px;width:300px;text-align:center;font-size:40px;font-weight:500;color:var(--ink)}
.utils{right:104px;top:64px;display:flex;align-items:center;gap:12px;font-size:16px}
.flag{width:12px;height:9px;background:#7d8fb8}
.badge{width:16px;height:16px;border-radius:50%;background:var(--c-navy);color:#fff;font-size:10px;display:flex;align-items:center;justify-content:center}
.rule{left:100px;top:122px;width:1000px;height:1px;background:var(--line)}
.nav{top:138px;left:0;width:1200px;display:flex;justify-content:center;gap:52px;font-size:16px;font-weight:500}
.hero{left:0;top:181px;width:1200px;height:513px;background:linear-gradient(90deg,#262626,#3a3a3a 60%,#2a2a2a)}
.hero-photo{position:absolute;left:540px;top:0;width:660px;height:513px;background:linear-gradient(180deg,#4a4341,#1b1b1b)}
.hero h2{position:absolute;left:100px;top:110px;color:#fff;font-weight:500;font-size:46px;line-height:1}
.hero h1{position:absolute;left:98px;top:162px;color:#fff;font-weight:500;font-size:94px;line-height:1}
.btn-light{position:absolute;left:105px;top:284px;width:166px;height:55px;background:#fff;border-radius:6px;font-size:17px;font-weight:500;display:flex;align-items:center;justify-content:center}
.cats{top:744px;left:98px;width:1002px;display:flex;gap:6px}
.cat{position:relative;flex:1;height:173px;border-radius:6px;overflow:hidden}
.cat span{position:absolute;left:20px;right:20px;bottom:10px;height:30px;background:#fff;border-radius:6px;font-size:13px;display:flex;align-items:center;justify-content:center}
.title{left:0;width:1200px;text-align:center;font-size:37px;font-weight:500}
.products{left:98px;width:1002px;display:flex;gap:11px}
.prod{flex:1;height:316px;background:var(--card)}
.prod .pic{position:relative;height:177px}
.tag{position:absolute;left:9px;background:#333;color:#fff;font-size:12px;padding:5px 17px;border-radius:12px}
.prod h3{text-align:center;font-weight:400;font-size:22px;margin-top:29px}
.price{text-align:center;font-size:18px;margin-top:8px}
.price s{font-size:14px;margin-right:4px}
.sw{display:flex;justify-content:center;gap:17px;margin-top:18px}
.sw i{width:19px;height:17px;display:block}
.cols{left:98px;width:1003px;display:flex;gap:13px}
.col{flex:1;text-align:center}
.col .pic{height:184px;border-radius:6px}
.col h3{font-weight:500;font-size:23px;margin-top:28px}
.col p{font-size:14px;font-weight:300;color:#666;line-height:21px;margin:12px 14px 0}
.btn-dark{display:inline-block;margin-top:24px;background:var(--ink);color:#fff;font-size:14px;padding:9px 15px;border-radius:5px}
.date{font-size:18px;margin-top:26px;font-weight:300}
.col h3.b{margin-top:10px}
footer{left:0;top:2954px;width:1200px;height:421px;background:var(--ink);color:#fff}
.flogo{position:absolute;left:101px;top:112px;font-size:52px;font-weight:500}
.fcol{position:absolute;top:48px;font-size:15px;line-height:30px}
.fcol h4{font-size:22px;font-weight:500;line-height:30px}
.fcol h4:after{content:"";display:block;width:28px;height:2px;background:#fff;margin:8px 0 10px}
.fcol small{font-size:14px;display:block;line-height:22px}
.email{position:absolute;left:810px;top:170px;width:275px;height:38px;background:#fff;border-radius:20px;color:#333;font-size:13px;display:flex;align-items:center;justify-content:space-between;padding:0 14px 0 20px}
.social{position:absolute;top:249px;width:30px;height:30px;border:1px solid #fff;border-radius:50%}
.frule{position:absolute;left:111px;top:325px;width:976px;height:1px;background:#999}
.copy{position:absolute;top:360px;width:1200px;text-align:center;font-size:16px}
</style>
</head>
<body>
<div class="abs promo">Populate this marketing banner to advertise a special promotion such as: Save 20% this weekend!</div>
<div class="abs search">Search
<svg width="16" height="16" viewBox="0 0 16 16"><circle cx="6.5" cy="6.5" r="5" fill="none" stroke="#333" stroke-width="2"/><line x1="10" y1="10" x2="14.5" y2="14.5" stroke="#333" stroke-width="2"/></svg></div>
<div class="abs brand">Bold Dawn</div>
<div class="abs utils"><span>+1 888-888-8888</span><span class="flag"></span>
<svg width="18" height="18" viewBox="0 0 18 18"><circle cx="9" cy="9" r="8" fill="none" stroke="#333"/><circle cx="9" cy="7" r="3" fill="none" stroke="#333"/></svg>
<svg width="20" height="18" viewBox="0 0 20 18"><path d="M1 2h3l2 10h10l2-7H5" fill="none" stroke="#333" stroke-width="1.4"/><circle cx="8" cy="15" r="1.4" fill="#333"/><circle cx="15" cy="15" r="1.4" fill="#333"/></svg>
<span class="badge">0</span></div>
<div class="abs rule"></div>
<nav class="abs nav"><span>CLOTHING MANUFACTURER</span><span>SHOP ALL</span><span>SHIRTS</span><span>WHOLESALERS</span><span>MENS CLOTHES</span><span>BRANDS</span></nav>

<section class="abs hero">
  <div class="hero-photo" role="img" aria-label="Woman and man in black t-shirts and sunglasses"></div>
  <h2>WELCOME TO</h2>
  <h1>BOLD DAWN</h1>
  <div class="btn-light">SHOP NOW</div>
</section>

<div class="abs cats">
  <div class="cat" role="img" aria-label="Clothing factory floor" style="background:linear-gradient(#d9dde4,#6f7890)"><span>CLOTHING MANUFACTURER</span></div>
  <div class="cat" role="img" aria-label="Stacked colourful fabrics" style="background:linear-gradient(120deg,#b6563e,#6b3e7e,#c59b3a)"><span>WHOLESALERS</span></div>
  <div class="cat" role="img" aria-label="Man in floral shirt under blue sky" style="background:linear-gradient(#5b9fd6,#cfe3f2)"><span>MENS CLOTHES</span></div>
  <div class="cat" role="img" aria-label="Group of smiling women" style="background:linear-gradient(#9a8a7a,#5a3d2c)"><span>WOMANS CLOTHES</span></div>
</div>

<h2 class="abs title" style="top:998px">FEATURED PRODUCTS</h2>
<div class="abs products" style="top:1077px">
  <div class="prod"><div class="pic" role="img" aria-label="Woman in white t-shirt" style="background:#e6e6e6"><span class="tag" style="top:12px">ON SALE</span><span class="tag" style="top:46px">SAVE 20%</span></div><h3>T Shirt</h3><div class="price"><s>$ 252.23</s>$25.3</div><div class="sw"><i style="background:var(--c-navy)"></i><i style="background:var(--c-slate)"></i><i style="background:var(--c-red)"></i><i style="background:var(--c-teal)"></i><i style="background:var(--c-pink)"></i></div></div>
  <div class="prod"><div class="pic" role="img" aria-label="Man in black t-shirt" style="background:#555"><span class="tag" style="top:12px">ON SALE</span><span class="tag" style="top:46px">SAVE 20%</span></div><h3>T Shirt</h3><div class="price"><s>$ 252.23</s>$25.3</div><div class="sw"><i style="background:var(--c-navy)"></i><i style="background:var(--c-slate)"></i><i style="background:var(--c-red)"></i><i style="background:var(--c-teal)"></i><i style="background:var(--c-pink)"></i></div></div>
  <div class="prod"><div class="pic" role="img" aria-label="Woman in white t-shirt by stone wall" style="background:linear-gradient(#a84a5a,#8a8a84)"><span class="tag" style="top:12px">ON SALE</span><span class="tag" style="top:46px">SAVE 20%</span></div><h3>T Shirt</h3><div class="price"><s>$ 252.23</s>$25.3</div><div class="sw"><i style="background:var(--c-navy)"></i><i style="background:var(--c-slate)"></i><i style="background:var(--c-red)"></i><i style="background:var(--c-teal)"></i><i style="background:var(--c-pink)"></i></div></div>
  <div class="prod"><div class="pic" role="img" aria-label="Man in white t-shirt by dark door" style="background:#3e5458"><span class="tag" style="top:12px">ON SALE</span><span class="tag" style="top:46px">SAVE 20%</span></div><h3>T Shirt</h3><div class="price"><s>$ 252.23</s>$25.3</div><div class="sw"><i style="background:var(--c-navy)"></i><i style="background:var(--c-slate)"></i><i style="background:var(--c-red)"></i><i style="background:var(--c-teal)"></i><i style="background:var(--c-pink)"></i></div></div>
</div>

<h2 class="abs title" style="top:1459px">ABOUT US</h2>
<div class="abs cols" style="top:1527px">
  <div class="col"><div class="pic" role="img" aria-label="Smiling business team" style="background:linear-gradient(#eee,#b9b3ac)"></div><h3>OUR TEAM</h3><p>Sed ut perspiciatis unde omnis iste natus error sit voluptatem accusantium doloremque laudantium, totam rem aperiam</p><span class="btn-dark">Learn More</span></div>
  <div class="col"><div class="pic" role="img" aria-label="Figure on mountain peak with target at sunrise" style="background:linear-gradient(#2f93a8,#d8e4c6)"></div><h3>OUR MISSION</h3><p>Sed ut perspiciatis unde omnis iste natus error sit voluptatem accusantium doloremque laudantium, totam rem aperiam</p><span class="btn-dark">Learn More</span></div>
  <div class="col"><div class="pic" role="img" aria-label="Hand touching rising growth line" style="background:linear-gradient(#a7d6e8,#c9e6ef)"></div><h3>OUR VALUES</h3><p>Sed ut perspiciatis unde omnis iste natus error sit voluptatem accusantium doloremque laudantium, totam rem aperiam</p><span class="btn-dark">Learn More</span></div>
</div>

<h2 class="abs title" style="top:1954px">NEW PRODUCTS</h2>
<div class="abs products" style="top:2034px">
  <div class="prod"><div class="pic" role="img" aria-label="Man in white t-shirt" style="background:#7fa5a6"><span class="tag" style="top:12px">ON SALE</span><span class="tag" style="top:46px">SAVE 20%</span></div><h3>T Shirt</h3><div class="price"><s>$ 252.23</s>$25.3</div><div class="sw"><i style="background:var(--c-navy)"></i><i style="background:var(--c-slate)"></i><i style="background:var(--c-red)"></i><i style="background:var(--c-teal)"></i><i style="background:var(--c-pink)"></i></div></div>
  <div class="prod"><div class="pic" role="img" aria-label="Older man in grey t-shirt" style="background:#6f9399"><span class="tag" style="top:12px">ON SALE</span><span class="tag" style="top:46px">SAVE 20%</span></div><h3>T Shirt</h3><div class="price"><s>$ 252.23</s>$25.3</div><div class="sw"><i style="background:var(--c-navy)"></i><i style="background:var(--c-slate)"></i><i style="background:var(--c-red)"></i><i style="background:var(--c-teal)"></i><i style="background:var(--c-pink)"></i></div></div>
  <div class="prod"><div class="pic" role="img" aria-label="Woman in white t-shirt" style="background:#d7b4b8"><span class="tag" style="top:12px">ON SALE</span><span class="tag" style="top:46px">SAVE 20%</span></div><h3>T Shirt</h3><div class="price"><s>$ 252.23</s>$25.3</div><div class="sw"><i style="background:var(--c-navy)"></i><i style="background:var(--c-slate)"></i><i style="background:var(--c-red)"></i><i style="background:var(--c-teal)"></i><i style="background:var(--c-pink)"></i></div></div>
  <div class="prod"><div class="pic" role="img" aria-label="Woman in white t-shirt giving thumbs up" style="background:#6fb0c6"><span class="tag" style="top:12px">ON SALE</span><span class="tag" style="top:46px">SAVE 20%</span></div><h3>T Shirt</h3><div class="price"><s>$ 252.23</s>$25.3</div><div class="sw"><i style="background:var(--c-navy)"></i><i style="background:var(--c-slate)"></i><i style="background:var(--c-red)"></i><i style="background:var(--c-teal)"></i><i style="background:var(--c-pink)"></i></div></div>
</div>

<h2 class="abs title" style="top:2452px">OUR BLOG</h2>
<div class="abs cols" style="top:2528px">
  <div class="col"><div class="pic" role="img" aria-label="Smiling woman in a cafe" style="background:linear-gradient(#3b3a33,#7a6a58)"></div><div class="date">AUG 22.2023</div><h3 class="b">HUMAN HAPPINESS</h3><p>Sed ut perspiciatis unde omnis iste natus error sit voluptatem accusantium doloremque laudantium, totam rem aperiam</p></div>
  <div class="col"><div class="pic" role="img" aria-label="Woman in printed black t-shirt in bright room" style="background:linear-gradient(90deg,#f2f2f2,#dcdcdc)"></div><div class="date">AUG 22.2023</div><h3 class="b">HUMAN HAPPINESS</h3><p>Sed ut perspiciatis unde omnis iste natus error sit voluptatem accusantium doloremque laudantium, totam rem aperiam</p></div>
  <div class="col"><div class="pic" role="img" aria-label="Smiling man in black t-shirt" style="background:linear-gradient(#2f2d28,#5a4a3a)"></div><div class="date">AUG 22.2023</div><h3 class="b">HUMAN HAPPINESS</h3><p>Sed ut perspiciatis unde omnis iste natus error sit voluptatem accusantium doloremque laudantium, totam rem aperiam</p></div>
</div>

<footer class="abs">
  <div class="flogo">Bold Dawn</div>
  <div class="fcol" style="left:363px"><h4>More Info</h4>Terms &amp; Conditions<br>Privacy Policy<br>About Us<br>Support</div>
  <div class="fcol" style="left:561px;top:46px"><h4>Contact Us</h4>
    <small>ADDRESS</small>
    <small><svg width="10" height="13" viewBox="0 0 10 13"><path d="M5 0a5 5 0 0 1 5 5c0 3-5 8-5 8S0 8 0 5a5 5 0 0 1 5-5z" fill="#fff"/><circle cx="5" cy="5" r="2" fill="#231f20"/></svg> Lorem ipsum dolor sit<br>amet, consecteturs</small>
    <small style="margin-top:12px">PHONE</small>
    <small><svg width="12" height="12" viewBox="0 0 12 12"><path d="M2 0l3 3-1.5 1.5a7 7 0 0 0 4 4L9 7l3 3-2 2C5 12 0 7 0 2z" fill="#fff"/></svg> +1 888-888-8888</small>
    <small style="margin-top:12px">EMAIL</small>
    <small><svg width="13" height="10" viewBox="0 0 13 10"><rect width="13" height="10" fill="#fff"/><path d="M0 0l6.5 5L13 0" stroke="#231f20" fill="none"/></svg> info@bolddawn.com</small>
  </div>
  <div class="fcol" style="left:812px;top:46px;width:290px"><h4>Newsletter</h4><small style="font-size:15px">Lorem ipsum dolor sit amet, consectetur adipiscing elit, sed do eiusmod tempor</small></div>
  <div class="email">Enter Email<svg width="18" height="18" viewBox="0 0 18 18"><circle cx="9" cy="9" r="9" fill="#231f20"/><path d="M4 9l10-4-3 9-2-3z" fill="#fff"/></svg></div>
  <span class="social" style="left:101px"></span>
  <span class="social" style="left:139px"></span>
  <div class="frule"></div>
  <div class="copy">© copyrights 2023 Bold Dawn &nbsp;|&nbsp; All Rights Reserved</div>
</footer>
</body>
</html>
```